Computer consultant business card

Bexil Software is a newly started computer consulting company. It's a small one-man company that provides mostly Vornix applications but also websites in collaboration with designers. I'm running this company on the side of full time university studies.

I want the final design to be clean and memorable. Be creative! :)

Some inspiration:
http://www.pixelmarta.com/design/48317
http://www.pixelmarta.com/design/2739164/business-card-design-by-frostlynk
http://www.pixelmarta.com/design/604281/business-card-design-by-koralind-vestrabanu

See attachment for my company logo.
Updates

I would like to thank everyone for submitting! I'll need a couple of days to review and ultimately select a design.

Target Market(s)

Non-technical entrepreneurs and small companies.

Industry/Entity Type

University

Requirements
Must have
• My company logo.
In any way, both colors from my logo.
First- and last name, e-mail and phone number.
Double-sided design.
Nice to have
• Something creative with the symbol in my logo

```html
<!DOCTYPE html>
<html lang="en">
<head>
<meta charset="utf-8">
<title>Bexil Software – Business Card</title>
<link rel="stylesheet" href="https://fonts.googleapis.com/css2?family=Open+Sans:wght@400;600&display=swap">
<style>
  :root {
    --backdrop: #e9eaec;
    --card-white: #f7f8f9;
    --brand-blue: #5b86c9;
    --brand-blue-light: #7099d6;
    --brand-dark: #4a4a4c;
    --soft-grey: #e0e2e6;
    --text-grey: #55565a;
  }
  * { box-sizing: border-box; margin: 0; padding: 0; }
  html, body {
    width: 1200px; height: 900px; overflow: hidden;
    background: var(--backdrop);
    font-family: "Open Sans", sans-serif;
  }
  .sheet {
    width: 1200px; height: 900px;
    display: flex; flex-direction: column;
    align-items: center; justify-content: center; gap: 54px;
  }
  .card {
    position: relative;
    width: 600px; height: 343px;
    background: var(--card-white);
    box-shadow: 0 6px 20px rgba(0,0,0,0.14);
    overflow: hidden;
  }

  /* Front */
  .card-front .panel {
    position: absolute; inset: 28px;
    background: linear-gradient(160deg, var(--brand-blue) 0%, var(--brand-blue-light) 100%);
    display: flex; align-items: center; justify-content: center;
  }
  .brand { display: flex; align-items: center; gap: 16px; }
  .brand-dot {
    width: 54px; height: 54px; border-radius: 50%;
    background: var(--card-white);
    flex: none;
  }
  .brand-text { display: flex; flex-direction: column; }
  .brand-name {
    font-weight: 600; font-size: 52px; line-height: 1;
    letter-spacing: 1px; color: #ffffff;
  }
  .brand-tagline {
    font-size: 12px; letter-spacing: 1.5px; color: #ffffff;
    margin-top: 4px;
  }

  /* Back */
  .card-back .corner-tab {
    position: absolute; right: 0; top: 0;
    width: 120px; height: 46px; background: var(--soft-grey);
  }
  .card-back .side-strip {
    position: absolute; left: 0; top: 196px; bottom: 0;
    width: 46px; background: var(--soft-grey);
  }
  .card-back .blue-band {
    position: absolute; left: 0; right: 0; top: 164px;
    height: 26px; background: var(--brand-blue);
  }
  .card-back .brand { position: absolute; left: 64px; top: 66px; }
  .card-back .brand-dot { background: var(--brand-blue); }
  .card-back .brand-name { color: var(--brand-dark); }
  .contact {
    position: absolute; left: 76px; top: 208px;
    list-style: none; color: var(--text-grey);
    font-size: 15px; line-height: 27px; letter-spacing: 0.3px;
  }
  .contact .person {
    font-weight: 600; color: var(--brand-dark);
  }
</style>
</head>
<body>
<main class="sheet">
  <section class="card card-front" aria-label="Card front">
    <div class="panel">
      <div class="brand">
        <span class="brand-dot"></span>
        <div class="brand-text">
          <span class="brand-name">bexil</span>
          <span class="brand-tagline">tagline / slogan / website</span>
        </div>
      </div>
    </div>
  </section>

  <section class="card card-back" aria-label="Card back">
    <div class="corner-tab"></div>
    <div class="side-strip"></div>
    <div class="blue-band"></div>
    <div class="brand">
      <span class="brand-dot"></span>
      <span class="brand-name">bexil</span>
    </div>
    <ul class="contact">
      <li class="person">Jonas Verhill</li>
      <li>218 Hollowmere Ave, Dunbridge NY 60482</li>
      <li>Tel: 2468 1357 &nbsp;-&nbsp; Fax: 2468 1358</li>
      <li>hello@bexilsoft.com</li>
    </ul>
  </section>
</main>
</body>
</html>
```